Luxury Real Estate Website, Midwest, United States

We need web design services for a luxury website. We need IDX Integration with our MLS. We want this to be a very simple website with amazing graphics. We want it to link up with our MailChimp account in order to generate leads through a "More Information" Pop up on the main page. We want the main page to be covered with one large graphic that is a rolling slideshow of active listings of $400,000 and up from the IDX Integration. We need this website to give a very exclusive and sleek look. Lots of black is good... I will upload our logos in Black and Silver. We will also need an "About" page that we are going to call "Qeno Info". We want our graphics to be extremely impressive. Keep in mind, we are a company in the Midwest of the United States, and our real estate has a different look than homes in California or Florida. We need graphics that are realistic for the Midwest, yet still high-end.
Target Market(s)
Luxury Homeowners in the Midwest United States. The graphics needs to be pristine.
Industry/Entity Type
Real Estate
Coding
Coded - Design and coding required
Number of Pages Required
3 page
Requirements
Must have
- Large graphics with IDX Integration. The photos of real estate need to represent real estate that is common in the Midwest, United States. We also need MailChimp integration. We need a pop up that is titled "My Free Market Analysis" that makes them fill out a contact form asking for Full Name, Email Address, Phone Number and Address. This needs to be a pop up on the front page and will integrate with our MailChimp account. We also need a page called "About Qe No Home". And another page where clients can download informational PDFs. The main component needs to be a front page search engine connected with the IDX to access active listings from our MLS. I attached our logos and a sample front page of a website. I would love for ours to look similar.
Nice to have
- Lake House photos on midwest lakes are a plus.
Should not have
- Should not have clutter. This website needs to be clean, luxurious and exclusive.

```html
<!DOCTYPE html>
<html lang="en">
<head>
<meta charset="utf-8">
<title>Northvale Realty Group — My Free Market Analysis</title>
<link rel="stylesheet" href="https://fonts.googleapis.com/css2?family=Roboto:ital,wght@0,300;0,400;0,500;0,700;0,900;1,400&family=Open+Sans:wght@400;600&display=swap">
<style>
:root{
  --page:#ececec;
  --ink:#111111;
  --muted:#6f6f6f;
  --faint:#d6d6d6;
  --footer:#202020;
  --footer-deep:#151515;
  --footer-text:#9a9a9a;
  --veil:rgba(8,8,8,.8);
  --field:#ffffff;
  --field-line:#d3d7da;
  --button:#c5d3e3;
  --button-line:#9fb2c8;
}
*{box-sizing:border-box;margin:0;padding:0}
html,body{width:1200px;height:3243px;overflow:hidden}
body{position:relative;background:var(--page);font-family:"Roboto",sans-serif;color:var(--ink)}
.abs{position:absolute}

/* header */
.site-header{left:0;top:0;width:1200px;height:91px;background:#f4f4f4;z-index:2}
.brand{display:flex;align-items:center;gap:12px;font-weight:400;color:var(--ink)}
.brand-mark{width:14px;height:14px;background:var(--ink)}
.site-header .brand{left:102px;top:26px;font-size:30px;letter-spacing:1px}
.main-nav{right:102px;top:36px;display:flex;gap:30px;font-size:14px}

/* hero */
.hero{left:0;top:91px;width:1200px;height:508px;
  background:
    linear-gradient(90deg,rgba(30,50,25,.85) 0%,rgba(30,50,25,0) 12%,rgba(30,50,25,0) 88%,rgba(30,50,25,.85) 100%),
    linear-gradient(180deg,#a9c4dc 0%,#cfd8df 22%,#9a7e62 38%,#7f6a58 48%,#6f9a4c 60%,#5d8a3e 70%,#6f8fa8 80%,#a4b9c8 100%)}

/* about */
.about-photo{left:151px;top:709px;width:381px;height:532px;
  background:linear-gradient(175deg,#7c8790 0%,#4c5762 30%,#2b3540 48%,#6e8fae 58%,#4f6a83 66%,#8b8f8c 76%,#5f6e4a 100%)}
.watermark-title{font-weight:900;color:var(--faint);letter-spacing:2px;line-height:1}
.about-title{left:558px;top:713px;font-size:92px}
.about-copy{left:564px;top:810px;width:492px;font-family:"Open Sans",sans-serif;font-size:13px;line-height:24px;color:var(--muted)}
.read-more{left:564px;top:953px;width:128px;height:37px;background:#3a3a3a;color:#fff;font-size:12px;letter-spacing:1px;display:flex;align-items:center;justify-content:center}
.about-thumb{top:1025px;width:227px;height:216px}
.thumb-a{left:564px;background:linear-gradient(170deg,#5f7d4a 0%,#a8c0cf 35%,#c0682c 62%,#7a4a25 80%,#3d3a30 100%)}
.thumb-b{left:822px;background:linear-gradient(170deg,#4f7a3e 0%,#9ab87a 35%,#3e5a2f 62%,#6c6750 100%)}

/* features */
.features-photo{left:642px;top:1356px;width:458px;height:257px;
  background:linear-gradient(180deg,#6d8a9a 0%,#3f5a52 28%,#2e3a2c 50%,#8a6a3c 66%,#47603a 82%,#2f3d30 100%)}
.features-title{left:95px;top:1440px;font-size:96px}
.feature{top:1692px;width:300px;text-align:center}
.feature svg{display:block;margin:0 auto 14px}
.feature h3{font-size:21px;font-weight:400;letter-spacing:.5px;margin-bottom:8px}
.feature p{font-family:"Open Sans",sans-serif;font-size:13px;line-height:20px;color:var(--muted);padding:0 22px}

/* properties */
.properties-title{left:525px;top:1946px;font-size:96px}
.properties-tab{left:99px;top:2017px}
.properties-tab span{position:absolute;left:35px;top:18px;font-size:32px;color:#fff}
.property-grid{left:99px;top:2089px;width:1001px;height:402px;display:grid;grid-template-columns:repeat(4,1fr);grid-template-rows:repeat(2,1fr)}
.property{position:relative}
.p1{background:linear-gradient(160deg,#f2f4f5 0%,#bfc7cd 40%,#5c666e 60%,#d7dcdf 100%)}
.p2{background:linear-gradient(160deg,#4a5563 0%,#2a323b 55%,#161b20 100%)}
.p3{background:linear-gradient(180deg,#7fb0de 0%,#a8c8e6 25%,#c0562e 45%,#8e4a30 58%,#4b7ea6 75%,#6a94b4 100%)}
.p4{background:linear-gradient(180deg,#b9cad8 0%,#8aa070 35%,#eceef0 50%,#6f9a4a 68%,#5a7c8e 100%)}
.p5{background:linear-gradient(180deg,#d9dee2 0%,#6a4d38 35%,#3f2e22 55%,#5e8a3e 80%,#4c7030 100%)}
.p6{background:linear-gradient(180deg,#93b4cc 0%,#4f7a36 35%,#6a9a48 60%,#eef1f2 70%,#6f8798 100%)}
.p7{background:linear-gradient(180deg,#c9d4dc 0%,#8a9aa3 35%,#5a4434 55%,#a3a8a6 75%,#7c7f7c 100%)}
.p8{background:linear-gradient(180deg,#b7c8d4 0%,#5d8848 35%,#eceff0 50%,#4e7088 70%,#2f5068 100%)}
.property-label{position:absolute;left:26px;top:88px;color:#fff;font-size:22px}

/* contact */
.footer-band{left:0;top:2731px;width:1200px;height:512px;background:var(--footer)}
.contact-card{left:141px;top:2605px;width:918px;height:260px;background:#fff;text-align:center}
.contact-card h2{margin-top:52px;font-size:34px;font-weight:300}
.contact-card p{margin-top:6px;font-size:20px;font-style:italic;color:#333}
.contact-form{position:absolute;left:89px;top:152px;width:710px;height:47px;display:flex;gap:14px}
.contact-form .input{flex:1;border-bottom:1px solid var(--field-line);font-size:13px;color:#999;display:flex;align-items:center;padding-left:10px}
.contact-form .send{width:136px;background:#1c2730;color:#fff;font-size:13px;display:flex;align-items:center;justify-content:center}

.footer-nav{left:0;top:2904px;width:1200px;display:flex;justify-content:center;gap:34px;font-size:13px;color:var(--footer-text);letter-spacing:.5px}
.footer-brand{left:0;top:2962px;width:1200px;justify-content:center;color:#cfcfcf;font-size:30px}
.footer-brand .brand-mark{background:#cfcfcf}
.contact-item{top:3048px;width:260px;text-align:center;color:var(--footer-text);font-size:13px;line-height:20px}
.contact-item .badge{width:46px;height:46px;border-radius:50%;border:1px solid #555;margin:0 auto 18px;display:flex;align-items:center;justify-content:center}
.contact-item .badge.solid{background:#3a3a3a}
.bottom-bar{left:0;top:3190px;width:1200px;height:53px;background:var(--footer-deep)}
.copyright{left:99px;top:3207px;font-size:12px;color:#777}
.social{top:3206px;width:18px;height:18px;border-radius:50%;background:#777}

/* veil + popup */
.veil{left:0;top:0;width:1200px;height:3243px;background:var(--veil);z-index:5}
.popup{left:99px;top:95px;width:1001px;height:482px;z-index:10;overflow:hidden;background:#fff}
.popup-photo{position:absolute;inset:0;
  background:linear-gradient(180deg,#f1f5f8 0%,#e6ebee 18%,#d9d0c4 32%,#cbbfb1 42%,#d6e2c4 54%,#cfdcbc 62%,#c9d7e2 72%,#d8cbb8 82%,#d3dfe8 100%)}
.popup .brand{position:absolute;left:0;right:0;top:74px;justify-content:center;font-size:26px}
.popup h1{position:absolute;left:0;right:0;top:144px;text-align:center;font-size:36px;font-weight:500}
.field{position:absolute;width:387px;height:43px;background:var(--field);border:1px solid var(--field-line);box-shadow:0 1px 3px rgba(0,0,0,.12);font-size:13px;color:#444;display:flex;align-items:center;padding-left:20px}
.submit{position:absolute;left:442px;top:374px;width:119px;height:41px;background:var(--button);border:1px solid var(--button-line);border-radius:3px;font-size:15px;display:flex;align-items:center;justify-content:center;letter-spacing:.5px}
.partner-badge{position:absolute;left:808px;top:411px;display:flex;align-items:center;gap:8px}
.partner-badge .dot{width:52px;height:52px;border-radius:50%;background:#3d3d3d}
.partner-badge .bar{width:100px;height:20px;border-radius:4px;background:#3d3d3d}
</style>
</head>
<body>

<header class="site-header abs">
  <div class="brand abs"><span class="brand-mark"></span>NORTHVALE</div>
  <nav class="main-nav abs"><span>Home</span><span>Qeno Info</span><span>About Qe No Home</span><span>Downloads</span><span>Contact us</span></nav>
</header>

<div class="hero abs" role="img" aria-label="Slideshow photo of a large Midwest lakefront home"></div>

<section class="about">
  <div class="about-photo abs" role="img" aria-label="Modern lake house with pool at dusk"></div>
  <div class="about-title watermark-title abs">ABOUT US</div>
  <p class="about-copy abs">We are a boutique team focused on lakefront and estate homes across the Midwest. We pair deep local knowledge with modern marketing to present every property at its very best, and we guide each client from the first showing to closing day with care, patience and complete discretion.</p>
  <div class="read-more abs">READ MORE</div>
  <div class="about-thumb thumb-a abs" role="img" aria-label="Lakeside deck with autumn trees"></div>
  <div class="about-thumb thumb-b abs" role="img" aria-label="Wooded lake cottage"></div>
</section>

<section class="features">
  <div class="features-title watermark-title abs">FEATURES</div>
  <div class="features-photo abs" role="img" aria-label="Lake house among trees at evening"></div>
  <div class="feature abs" style="left:105px">
    <svg width="44" height="44" viewBox="0 0 44 44"><circle cx="22" cy="22" r="19" fill="none" stroke="#666" stroke-width="3"/><path d="M22 11v12l8 5" fill="none" stroke="#666" stroke-width="3" stroke-linecap="round"/></svg>
    <h3>EFFICIENCY</h3>
    <p>Fast answers and clear steps from the first listing call to closing day, every time.</p>
  </div>
  <div class="feature abs" style="left:449px">
    <svg width="44" height="44" viewBox="0 0 44 44"><path d="M4 22L22 6l18 16h-5v16h-9V28h-8v10H9V22z" fill="#666"/></svg>
    <h3>PROPERTY LISTINGS</h3>
    <p>Browse active homes from the MLS with full photos, prices and detailed property facts.</p>
  </div>
  <div class="feature abs" style="left:795px">
    <svg width="44" height="44" viewBox="0 0 44 44"><circle cx="14" cy="12" r="5" fill="#666"/><circle cx="30" cy="12" r="5" fill="#666"/><circle cx="7" cy="24" r="4" fill="#666"/><circle cx="37" cy="24" r="4" fill="#666"/><ellipse cx="22" cy="31" rx="10" ry="8" fill="#666"/></svg>
    <h3>EXPERTISE</h3>
    <p>Years of local market insight on lakes, acreage and fine estates across the region.</p>
  </div>
</section>

<section class="properties">
  <div class="properties-title watermark-title abs">PROPERTIES</div>
  <div class="properties-tab abs">
    <svg width="377" height="72" viewBox="0 0 377 72"><path d="M0 0H330L377 72H0z" fill="#2b2b2b"/></svg>
    <span>Our Properties</span>
  </div>
  <div class="property-grid abs">
    <div class="property p1" role="img" aria-label="White modern home facade"></div>
    <div class="property p2" role="img" aria-label="Luxury lake house at night"><span class="property-label">Luxury Lake House</span></div>
    <div class="property p3" role="img" aria-label="Lakefront home with boat dock"></div>
    <div class="property p4" role="img" aria-label="Lake house on a grassy shore"></div>
    <div class="property p5" role="img" aria-label="Timber lodge style home"></div>
    <div class="property p6" role="img" aria-label="Lake home among trees"></div>
    <div class="property p7" role="img" aria-label="Covered porch overlooking a lake"></div>
    <div class="property p8" role="img" aria-label="Lakeside home with pier"></div>
  </div>
</section>

<footer>
  <div class="footer-band abs"></div>
  <div class="contact-card abs">
    <h2>Want To Know More ?</h2>
    <p>Leave your feedback or request for direct contact here.</p>
    <div class="contact-form"><div class="input">Your Email</div><div class="send">SEND</div></div>
  </div>
  <nav class="footer-nav abs"><span>HOME</span><span>QENO INFO</span><span>ABOUT QE NO HOME</span><span>DOWNLOADS</span><span>CONTACT US</span></nav>
  <div class="brand footer-brand abs"><span class="brand-mark"></span>NORTHVALE</div>
  <div class="contact-item abs" style="left:209px">
    <div class="badge"><svg width="18" height="22" viewBox="0 0 18 22"><path d="M9 1a7 7 0 0 0-7 7c0 5 7 13 7 13s7-8 7-13a7 7 0 0 0-7-7z" fill="none" stroke="#888" stroke-width="1.6"/><circle cx="9" cy="8" r="2.5" fill="#888"/></svg></div>
    2140 Harbor Point Drive,<br>Lake Geneva, WI 53147
  </div>
  <div class="contact-item abs" style="left:480px">
    <div class="badge solid"><svg width="20" height="20" viewBox="0 0 20 20"><path d="M5 2l3 4-2 2c1 3 3 5 6 6l2-2 4 3-2 3C9 18 2 11 2 4z" fill="#aaa"/></svg></div>
    (262) 555-0148
  </div>
  <div class="contact-item abs" style="left:763px">
    <div class="badge"><svg width="22" height="16" viewBox="0 0 22 16"><rect x="1" y="1" width="20" height="14" fill="none" stroke="#888" stroke-width="1.6"/><path d="M1 1l10 8 10-8" fill="none" stroke="#888" stroke-width="1.6"/></svg></div>
    hello@northvalerealty.com
  </div>
  <div class="bottom-bar abs"></div>
  <div class="copyright abs">© 2024 Northvale Realty Group. All Rights Reserved.</div>
  <span class="social abs" style="left:1044px"></span>
  <span class="social abs" style="left:1074px"></span>
  <span class="social abs" style="left:1104px"></span>
</footer>

<div class="veil abs"></div>

<div class="popup abs" role="dialog" aria-label="My Free Market Analysis">
  <div class="popup-photo" role="img" aria-label="Faded photo of a lakeside Midwest home with lawn and water"></div>
  <div class="brand"><span class="brand-mark"></span>NORTHVALE</div>
  <h1>My Free Market Analysis</h1>
  <div class="field" style="left:98px;top:221px">Full Name</div>
  <div class="field" style="left:517px;top:221px">Email Address</div>
  <div class="field" style="left:98px;top:292px">Phone Number</div>
  <div class="field" style="left:517px;top:292px">Address</div>
  <div class="submit">SUBMIT</div>
  <div class="partner-badge"><span class="dot"></span><span class="bar"></span></div>
</div>

</body>
</html>
```